Business Card Design - Property Management & Real Estate Services

I need a business card design for my company that I can print ZEPLA Cards. The company is called Brindle Management Company. It is a property management and real estate company. The design has to be clean and modern. I need two versions. One for my employee and one for me. However, the design will be the same, just different text. You can get a feel for the company by looking at our website at www.brindlemanagement.example.

Industry/Entity Type

Property Management

Contact Information for Business Card

I will be using ZEPLA.com to print my cards. I will most likely use the rounded edges card. I need two versions, however, they will be the same design. I need one for me and my employee.

Colors
3276b5
33a6d7

Requirements
Must have
• Company Logo
• Name of person
• Property Management & Real Estate Service
• Phone
• Email
• Website
• Address
• A space to place a QR code

```html
<!DOCTYPE html>
<html lang="en">
<head>
<meta charset="utf-8">
<title>Brindle Management – Business Card</title>
<link href="https://fonts.googleapis.com/css2?family=Roboto:wght@400;500&family=Fira+Sans+Condensed:wght@600&display=swap" rel="stylesheet">
<style>
  :root {
    --backdrop: #c9c9c9;
    --card-front: #6699cc;
    --brand-deep: #1f58a8;
    --brand-mid: #3276b5;
    --rule: #5a8fc8;
    --paper: #f8f8f8;
    --ink: #3a3a3a;
    --ink-soft: #555555;
  }
  * { margin: 0; padding: 0; box-sizing: border-box; }
  html, body { width: 1200px; height: 852px; overflow: hidden; }
  body {
    background: var(--backdrop);
    font-family: "Roboto", Arial, sans-serif;
    position: relative;
  }
  .card {
    position: absolute;
    width: 540px;
    height: 310px;
    border-radius: 16px;
    box-shadow: 0 6px 14px rgba(0,0,0,0.22);
    overflow: hidden;
  }
  .card-front {
    left: 90px; top: 90px;
    background: var(--card-front);
    display: flex; align-items: center; justify-content: center;
  }
  .front-wordmark {
    font-weight: 500;
    color: var(--brand-deep);
    text-align: center;
    font-size: 40px;
    letter-spacing: 4px;
    line-height: 1.15;
    text-transform: uppercase;
  }
  .card-back {
    left: 570px; top: 450px;
    background: var(--paper);
  }
  .back-wordmark {
    position: absolute;
    left: 34px; top: 92px;
    font-weight: 500;
    color: var(--brand-deep);
    font-size: 26px;
    letter-spacing: 2px;
    text-transform: uppercase;
    line-height: 1.15;
  }
  .wordmark-rule {
    position: absolute;
    left: 34px; top: 162px;
    width: 250px; height: 2px;
    background: var(--rule);
  }
  .services {
    position: absolute;
    left: 34px; top: 172px;
    font-size: 11px;
    letter-spacing: 0.3px;
    color: var(--brand-mid);
    white-space: nowrap;
  }
  .person {
    position: absolute;
    right: 34px; top: 34px;
    text-align: right;
  }
  .person-name {
    font-family: "Fira Sans Condensed", "Arial Narrow", sans-serif;
    font-weight: 600;
    font-size: 21px;
    color: var(--brand-deep);
  }
  .person-title {
    font-size: 13px;
    color: var(--ink);
    margin-top: 2px;
  }
  .person-rule {
    position: absolute;
    right: 34px; top: 92px;
    width: 230px; height: 1px;
    background: var(--rule);
  }
  .address {
    position: absolute;
    right: 34px; top: 108px;
    text-align: right;
    font-size: 13.5px;
    line-height: 1.45;
    color: var(--ink);
  }
  .qr-space {
    position: absolute;
    right: 34px; top: 206px;
    width: 70px; height: 70px;
    border: 1px dashed var(--rule);
    border-radius: 4px;
    background: #ffffff;
  }
  .contact-rule {
    position: absolute;
    left: 34px; top: 214px;
    width: 290px; height: 1px;
    background: var(--rule);
  }
  .contacts {
    position: absolute;
    left: 34px; top: 224px;
    list-style: none;
    font-size: 13.5px;
    color: var(--ink);
  }
  .contacts li {
    display: flex; align-items: center; gap: 8px;
    height: 21px;
  }
  .contacts svg { width: 12px; height: 12px; fill: var(--brand-mid); flex: none; }
</style>
</head>
<body>
  <section class="card card-front" aria-label="Card front">
    <div class="front-wordmark">Brindle<br>Management</div>
  </section>

  <section class="card card-back" aria-label="Card back">
    <div class="back-wordmark">Brindle<br>Management</div>
    <div class="wordmark-rule"></div>
    <div class="services">Property Management &amp; Real Estate Services</div>

    <div class="person">
      <div class="person-name">Tomas R. Almeda</div>
      <div class="person-title">Founder</div>
    </div>
    <div class="person-rule"></div>

    <div class="address">480 Harbor Ave<br>#210 Miami, FL 33130</div>

    <div class="qr-space" role="img" aria-label="Space reserved for a QR code"></div>

    <div class="contact-rule"></div>
    <ul class="contacts">
      <li>
        <svg viewBox="0 0 12 12" aria-hidden="true"><path d="M2.5 1h2l1 2.5-1.3 1a6 6 0 0 0 3.3 3.3l1-1.3 2.5 1v2a1 1 0 0 1-1 1A9.5 9.5 0 0 1 1.5 2a1 1 0 0 1 1-1z"/></svg>
        (305) 555-0142
      </li>
      <li>
        <svg viewBox="0 0 12 12" aria-hidden="true"><path d="M1 2.5h10v7H1z M1.5 3l4.5 3.5L10.5 3" stroke="#f8f8f8" stroke-width="0.9"/></svg>
        tomas@brindlemanagement.example
      </li>
      <li>
        <svg viewBox="0 0 12 12" aria-hidden="true"><circle cx="6" cy="6" r="5"/><path d="M1 6h10M6 1c-2.5 3-2.5 7 0 10M6 1c2.5 3 2.5 7 0 10" stroke="#f8f8f8" stroke-width="0.8" fill="none"/></svg>
        www.brindlemanagement.example
      </li>
    </ul>
  </section>
</body>
</html>
```